Professional Website for Leading Global Private Equity Real Estate Company

The company is a leading global Private Equity Real Estate (PERE). We need a homepage design, an inner page design, and color/font tweaks to the logo (color should be more soothing than current blue used in the logo). The logo website should project the company as global, professional, experienced, trustworthy, accessible, YOUNG, DYNAMIC, hi-tech. PLEASE SEE the attached Design Brief Word Doc for details.

Target Market(s)

institional investors and wealthy private individuals

Industry/Entity Type

Finance

Number of Pages Required

2 page

Font styles to use
Sans Serif
Other font styles liked:
• either like in https://www.ferndalequay.com/ or like in presentations (Montserrat Black & Montserrat Light, Century Gothic, Blair ITC, Almoni Neue DL 4.0 AAA Medium, Almoni DL AAA)

Requirements
Must have
• new color palette that is NOT based on current logo. they want a more soothing color palette than the blue in that logo. the new color palette should project: global, professional, experienced, trustworthy, accessible, YOUNG, DYNAMIC, hi-tech.
Nice to have
• the likes these sites: https://www.ferndalequay.com/ and https://www.tvr.law/

```html
<!DOCTYPE html>
<html lang="en">
<head>
<meta charset="utf-8">
<title>Veltara Real Estate</title>
<link rel="stylesheet" href="https://fonts.googleapis.com/css2?family=Montserrat:wght@300;400;500;600;700;800&family=Arimo:wght@400;700&display=swap">
<style>
:root{
  --sky:#3fbdf5;
  --sky-deep:#29a9ea;
  --ink:#222428;
  --body:#555a60;
  --light:#f1f1f1;
  --footer:#1d1d1f;
  --white:#ffffff;
}
*{box-sizing:border-box;margin:0;padding:0}
html,body{width:1200px;height:5146px;overflow:hidden}
body{font-family:"Arimo",Arial,sans-serif;color:var(--body);background:var(--white);position:relative}
.head{font-family:"Montserrat",sans-serif}
.accent{color:var(--sky)}
.btn{display:inline-flex;align-items:center;justify-content:center;font-family:"Montserrat",sans-serif;font-weight:500;text-transform:uppercase;border-radius:30px;font-size:14px}
.btn-solid{background:var(--sky);color:var(--white)}
.btn-line{border:1.5px solid var(--sky);color:var(--sky);background:transparent;width:138px;height:50px;font-size:13px}
.bar{width:60px;height:3px;background:var(--sky)}

/* hero */
.hero{position:absolute;top:0;left:0;width:1200px;height:764px;background:linear-gradient(160deg,#6b6258 0%,#3e3a36 45%,#2b2b2e 100%)}
.hero::after{content:"";position:absolute;inset:0;background:rgba(20,22,26,.35)}
.nav{position:absolute;top:40px;left:110px;right:110px;height:40px;display:flex;align-items:center;z-index:2}
.brand{display:flex;align-items:center;gap:10px;color:var(--white);font-family:"Montserrat",sans-serif;font-weight:500;font-size:17px;letter-spacing:1px}
.brand .dot{width:22px;height:22px;border-radius:50%;background:var(--white)}
.menu{margin-left:auto;display:flex;gap:28px;align-items:center;list-style:none}
.menu a{color:var(--white);font-family:"Montserrat",sans-serif;font-size:11px;font-weight:500;text-decoration:none}
.menu .login{background:var(--sky);border-radius:20px;padding:10px 26px}
.hero-copy{position:absolute;top:340px;left:0;width:1200px;text-align:center;color:var(--white);z-index:2}
.hero-title{display:inline-flex;align-items:center;gap:12px;font-size:88px;font-weight:600;letter-spacing:2px;line-height:1}
.hero-title::before,.hero-title::after{content:"";width:44px;border-top:2px solid rgba(255,255,255,.8)}
.hero-sub{margin-top:18px;font-size:32px;font-weight:600}
.hero .btn{margin-top:30px;width:162px;height:54px;font-size:15px}

/* about */
.about{position:absolute;top:764px;left:0;width:1200px;height:386px;background:var(--sky);color:var(--white);text-align:center}
.about h2{margin-top:40px;font-size:38px;font-weight:600}
.about p{width:730px;margin:16px auto 0;font-size:13px;line-height:24px}
.countdown{position:absolute;left:260px;top:194px;width:680px;height:144px;border:1px solid rgba(255,255,255,.5);display:flex;justify-content:space-around;align-items:center}
.unit{width:120px}
.unit b{display:block;font-family:"Montserrat",sans-serif;font-weight:300;font-size:60px;line-height:1}
.unit span{display:block;margin-top:14px;font-family:"Montserrat",sans-serif;font-size:16px;font-weight:500}
.colon{font-size:44px;font-weight:300}

/* platforms */
.platforms-title{position:absolute;top:1198px;left:0;width:1200px;text-align:center;font-size:37px;font-weight:600;color:var(--ink)}
.platforms-bar{position:absolute;top:1258px;left:570px}
.row{position:absolute;left:110px;width:980px;height:300px}
.row .photo{position:absolute;top:0;width:490px;height:300px}
.row .text{position:absolute;top:0;width:490px;height:300px;padding:26px 8px 0 50px}
.row.right .photo{left:0}.row.right .text{left:490px}
.row.left .photo{left:490px}.row.left .text{left:0;padding-left:0;padding-right:50px}
.text h3{font-family:"Montserrat",sans-serif;font-size:22px;font-weight:500;color:var(--ink)}
.text .bar{margin:18px 0 26px;width:44px}
.text p{font-size:13px;line-height:27px;text-align:justify;color:var(--body)}
.text .btn{margin-top:26px}

/* edge */
.edge{position:absolute;top:2870px;left:0;width:1200px;height:512px;background:var(--light)}
.edge .photo{position:absolute;right:0;top:0;width:720px;height:512px;background:linear-gradient(90deg,var(--light) 0%,#b7bfc8 35%,#6d7886 100%)}
.edge .copy{position:absolute;left:110px;top:88px;width:400px}
.sec-title{font-size:34px;font-weight:600;color:var(--ink);white-space:nowrap;line-height:40px}
.copy .bar{margin:14px 0 24px}
.copy p{font-size:12.5px;line-height:24px;text-align:justify}
.copy .btn{margin-top:28px;height:56px;padding:0 24px;font-size:15px}

/* updated */
.updated{position:absolute;top:3382px;left:0;width:1200px;height:368px;text-align:center}
.updated h2{margin-top:56px;font-size:44px;font-weight:600;color:var(--ink)}
.updated p{width:680px;margin:24px auto 0;font-size:13px;line-height:24px}
.subscribe{width:760px;height:58px;margin:34px auto 0;display:flex;border:1px solid #cfd3d6;border-radius:30px;overflow:hidden}
.subscribe .email-hint{flex:1;text-align:left;padding:0 24px;line-height:56px;font-size:13px;color:#555}
.subscribe .btn{flex:none;border-radius:0 30px 30px 0;width:128px;height:56px;font-size:16px;color:var(--white)}

/* responsibility */
.resp{position:absolute;top:3750px;left:0;width:1200px;height:456px;background:var(--light)}
.resp .photo{position:absolute;left:0;top:0;width:612px;height:456px;background:linear-gradient(130deg,#5d5650,#2f2d2c 60%,#4a4640)}
.resp .copy{position:absolute;left:672px;top:60px;width:400px}
.resp .sec-title{font-size:33px}
.resp .copy .btn{margin-top:24px;height:56px;padding:0 30px}

/* contact */
.contact{position:absolute;top:4206px;left:0;width:1200px;height:530px;background:linear-gradient(180deg,var(--sky),var(--sky-deep));text-align:center;color:var(--white)}
.contact h2{margin-top:58px;font-size:34px;font-weight:600}
.contact .bar{background:var(--white);margin:14px auto 0}
.form{position:absolute;left:306px;top:140px;width:588px}
.field{border:1px solid rgba(255,255,255,.75);height:50px;text-align:left;padding:14px 18px;font-size:15px;position:absolute}
.contact .send{position:absolute;left:504px;top:404px;width:192px;height:62px;background:var(--footer);color:var(--white);border-radius:32px;font-size:17px;font-weight:600}

/* footer */
.footer{position:absolute;top:4736px;left:0;width:1200px;height:410px;background:var(--footer);color:var(--white)}
.fcol{position:absolute;top:58px}
.fcol h4{font-family:"Montserrat",sans-serif;font-size:18px;font-weight:500}
.links{list-style:none;margin-top:24px}
.links li{font-size:12px;font-weight:700;line-height:34px;font-family:"Montserrat",sans-serif}
.links li::before{content:"»";margin-right:18px}
.fcol p{font-size:12px;line-height:24px;margin-top:30px;width:360px}
.fcol a{color:var(--sky);font-size:12px;display:inline-block;margin-top:26px}
.info{display:flex;gap:16px;align-items:center;margin-top:22px}
.info svg{flex:none}
.info b{display:block;font-size:12px;font-weight:400;font-family:"Montserrat",sans-serif}
.info small{font-size:11px;line-height:20px}
.copyright{position:absolute;bottom:14px;left:0;width:1200px;text-align:center;font-size:13px}
.copyright a{color:var(--white)}
</style>
</head>
<body>

<header class="hero">
  <nav class="nav">
    <div class="brand"><span class="dot"></span>VELTARA REAL ESTATE</div>
    <ul class="menu">
      <li><a href="#">ABOUT US</a></li>
      <li><a href="#">OUR BUSINESSES</a></li>
      <li><a href="#">INVESTORS</a></li>
      <li><a href="#">LOBBY</a></li>
      <li><a href="#">NEWS</a></li>
      <li><a href="#">CONTACT US</a></li>
      <li><a class="login" href="#">LOGIN</a></li>
    </ul>
  </nav>
  <div class="hero-copy head" role="img" aria-label="Background photo of a young couple reviewing property on a laptop">
    <div class="hero-title">VELTARA</div>
    <div class="hero-sub">SED UT PERSPICIATIS UNDE OMNIS ISTE</div>
    <span class="btn btn-solid">About Us</span>
  </div>
</header>

<section class="about">
  <h2 class="head">ABOUT US</h2>
  <p>Sed ut perspiciatis unde omnis iste natus error sit voluptatem accusantium doloremque laudantium, totam rem eaque ipsa quae ab illo inventore veritatis et quasi architecto beatae vitae dicta sunt explicaboNemo enim ipsam voluptatem sed quia consequuntur magni dolores eos qui ratione voluptatem sequi nesciunt</p>
  <div class="countdown">
    <div class="unit"><b>35</b><span>DAYS</span></div><span class="colon">:</span>
    <div class="unit"><b>17</b><span>HOURS</span></div><span class="colon">:</span>
    <div class="unit"><b>59</b><span>MINUTES</span></div><span class="colon">:</span>
    <div class="unit"><b>56</b><span>SECONDS</span></div>
  </div>
</section>

<section class="platforms">
  <h2 class="platforms-title head">OUR INVESTMENT <span class="accent">PLATFORMS</span></h2>
  <div class="bar platforms-bar"></div>

  <article class="row right" style="top:1308px">
    <div class="photo" role="img" aria-label="Photo of hands passing a house model and keys" style="background:linear-gradient(135deg,#c99a6a,#8a6a52 55%,#e8e2da)"></div>
    <div class="text"><h3>Sed ut perspiciatis unde omnis</h3><div class="bar"></div>
      <p>Nemo enim ipsam voluptatem quia voluptas sit aspernatur aut odit aut fugit, sed quia consequuntur magni dolores eos qui ratione voluptatem sequi nesciunt. Neque porro quisquam est, qui dolorem ipsum quia dolor sit amet, consectetur</p>
      <span class="btn btn-line">Read More</span></div>
  </article>

  <article class="row left" style="top:1608px">
    <div class="text"><h3>Sed ut perspiciatis unde omnis</h3><div class="bar"></div>
      <p>Nemo enim ipsam voluptatem quia voluptas sit aspernatur aut odit aut fugit, sed quia consequuntur magni dolores eos qui ratione voluptatem sequi nesciunt. Neque porro quisquam est, qui dolorem ipsum quia dolor sit amet, consectetur</p>
      <span class="btn btn-line">Read More</span></div>
    <div class="photo" role="img" aria-label="Photo of an agent shaking hands with a couple in an office" style="background:linear-gradient(135deg,#d9d6d0,#7c7a78 50%,#c8b89c)"></div>
  </article>

  <article class="row right" style="top:1908px">
    <div class="photo" role="img" aria-label="Photo of coin stacks with a rising arrow beside house models" style="background:linear-gradient(135deg,#3a2e26,#6b4a2e 55%,#b88a52)"></div>
    <div class="text"><h3>Sed ut perspiciatis unde omnis</h3><div class="bar"></div>
      <p>Nemo enim ipsam voluptatem quia voluptas sit aspernatur aut odit aut fugit, sed quia consequuntur magni dolores eos qui ratione voluptatem sequi nesciunt. Neque porro quisquam est, qui dolorem ipsum quia dolor sit amet, consectetur</p>
      <span class="btn btn-line">Read More</span></div>
  </article>

  <article class="row left" style="top:2208px">
    <div class="text"><h3>Sed ut perspiciatis unde omnis</h3><div class="bar"></div>
      <p>Nemo enim ipsam voluptatem quia voluptas sit aspernatur aut odit aut fugit, sed quia consequuntur magni dolores eos qui ratione voluptatem sequi nesciunt. Neque porro quisquam est, qui dolorem ipsum quia dolor sit amet, consectetur</p>
      <span class="btn btn-line">Read More</span></div>
    <div class="photo" role="img" aria-label="Photo of a house model and charts on a desk" style="background:linear-gradient(135deg,#8a8479,#cfd2d4 50%,#5a5650)"></div>
  </article>

  <article class="row right" style="top:2508px">
    <div class="photo" role="img" aria-label="Photo of a team holding house models over a table" style="background:linear-gradient(135deg,#c9a278,#6e5a48 55%,#d8cfc4)"></div>
    <div class="text"><h3>Sed ut perspiciatis unde omnis</h3><div class="bar"></div>
      <p>Nemo enim ipsam voluptatem quia voluptas sit aspernatur aut odit aut fugit, sed quia consequuntur magni dolores eos qui ratione voluptatem sequi nesciunt. Neque porro quisquam est, qui dolorem ipsum quia dolor sit amet, consectetur</p>
      <span class="btn btn-line">Read More</span></div>
  </article>
</section>

<section class="edge">
  <div class="photo" role="img" aria-label="Photo of smiling colleagues in a business meeting"></div>
  <div class="copy">
    <h2 class="sec-title head">OUR <span class="accent">EDGE</span></h2>
    <div class="bar"></div>
    <p>Sed ut perspiciatis unde omnis iste natus error sit voluptatem acc usantium doloremque laudantium, totam rem aperiam, eaque ipsa quae ab illo inventore veritatis et quasi architecto beatae vitae dicta sunt explicabo. Nemo enim ipsam voluptatem quia volu ptas sit aspernatur aut odit aut fugit, sed quia consequuntur magni dolores eos qui ratione voluptatem sequi nesciunt. Neque porro quisquam est, qui dolorem ipsum quia dolor sit amet, consectetur, ut labore et dolore magnam aliquam quaerat voluptatem.</p>
    <span class="btn btn-solid">Investor Information</span>
  </div>
</section>

<section class="updated">
  <h2 class="head">STAY <span class="accent">UPDATED</span></h2>
  <p>Sed ut perspiciatis unde omnis iste natus error sit voluptatem accusantium doloremque laudantium, totam rem aperiam, eaque ipsa quae ab illo inventore veritatis et</p>
  <div class="subscribe"><span class="email-hint">Enter Your Email :</span><span class="btn btn-solid">Submit</span></div>
</section>

<section class="resp">
  <div class="photo" role="img" aria-label="Photo of two businessmen reviewing financial charts"></div>
  <div class="copy">
    <h2 class="sec-title head">OUR <span class="accent">RESPONSIBILITY</span></h2>
    <div class="bar"></div>
    <p>Sed ut perspiciatis unde omnis iste natus error sit voluptatem acc usantium doloremque laudantium, totam rem aperiam, eaque ipsa quae ab illo inventore veritatis et quasi architecto beatae vitae dicta sunt explicabo. Nemo enim ipsam voluptatem quia volu ptas sit aspernatur aut odit aut fugit, sed quia consequuntur magni dolores eos qui ratione voluptatem sequi nesciunt. Neque porro quisquam est, qui dolorem ipsum quia dolor sit amet, consectetur, ut labore et dolore magnam aliquam quaerat voluptatem.</p>
    <span class="btn btn-solid">Read More</span>
  </div>
</section>

<section class="contact">
  <h2 class="head">GET IN TOUCH</h2>
  <div class="bar"></div>
  <div class="form">
    <div class="field" style="left:0;top:0;width:288px">First Name :</div>
    <div class="field" style="left:300px;top:0;width:288px">Last Name :</div>
    <div class="field" style="left:0;top:64px;width:288px">Email :</div>
    <div class="field" style="left:300px;top:64px;width:288px">Phone :</div>
    <div class="field" style="left:0;top:126px;width:588px;height:118px">Message :</div>
  </div>
  <span class="btn send">Submit</span>
</section>

<footer class="footer">
  <div class="fcol" style="left:112px">
    <h4>IMPORTANT LINKS</h4>
    <ul class="links">
      <li>ABOUT US</li><li>OUR BUSINESSES</li><li>INVESTORS</li><li>LOBBY</li><li>NEWS</li><li>CONTACT US</li>
    </ul>
  </div>
  <div class="fcol" style="left:406px">
    <h4>EXPLORE VELTARA REAL ESTATE</h4>
    <p>Sed ut perspiciatis unde omnis iste natus error sit volupt atem accusantium doloremque laudantium, totam rem aperiam, eaque ipsa quae ab illo</p>
    <a href="#">Veltara America | Apartments</a>
  </div>
  <div class="fcol" style="left:842px">
    <h4>ADDRESS</h4>
    <div class="info">
      <svg width="40" height="40" viewBox="0 0 40 40"><circle cx="20" cy="20" r="19" fill="none" stroke="#fff" stroke-width="1.5"/><path d="M20 12a5 5 0 0 0-5 5c0 4 5 10 5 10s5-6 5-10a5 5 0 0 0-5-5z" fill="#fff"/><circle cx="20" cy="17" r="1.8" fill="#1d1d1f"/></svg>
      <div><b>ADDRESS</b><small># Lorem Ipsum Dummy Lorem</small></div>
    </div>
    <div class="info">
      <svg width="40" height="40" viewBox="0 0 40 40"><circle cx="20" cy="20" r="19" fill="none" stroke="#fff" stroke-width="1.5"/><path d="M15 13l3 0 1.5 4-2 1.5a9 9 0 0 0 4 4l1.5-2 4 1.5v3a2 2 0 0 1-2 2A13 13 0 0 1 13 15a2 2 0 0 1 2-2z" fill="#fff"/></svg>
      <div><b>PHONE</b><small>000-121-1231</small></div>
    </div>
    <div class="info">
      <svg width="40" height="40" viewBox="0 0 40 40"><circle cx="20" cy="20" r="19" fill="none" stroke="#fff" stroke-width="1.5"/><rect x="12" y="14" width="16" height="12" rx="1.5" fill="#fff"/><path d="M12.5 15l7.5 6 7.5-6" fill="none" stroke="#1d1d1f" stroke-width="1.4"/></svg>
      <div><b>EMAIL US</b><small>info@companyname.com</small></div>
    </div>
  </div>
  <div class="copyright">© Copyright 2022 Veltara.All Rights Reserved.<a href="#">Terms and Conditions Privacy Policy</a></div>
</footer>

</body>
</html>
```